Recruitment Ad for Social Media Marketing

Ad used to recruit Mortgage Originators

Target Market(s)

Real Estate Agents

Colors

Designer to choose colors to be used in the design.

Requirements
Must have
• HOMEBROKERS
• If you can send a text message, you can earn Mortgage Originator Income too...
• at Brightpath Lending Partners, "If you open the Brightpath door, We'll carry the load"
• We reimburse 100% of Licensing Costs
• * Immediate Payouts
• * Up to 75% Commission Split
• * No Goals or Quotas
• * Manage Your Own Schedule
• * Work from Home
• Send Resume to Careers@brightpathlendmail.com
• Brightpath Lending Partners, Inc.
• 7200 Marlowe Avenue, Ellicott City, MD 21046
• (800) 461-9027 Ext. 23
• NMLS #318764
• (SMALL PRINT AT BOTTOM)
• **Dual income requirements governed by state law. In most cases, Homebrokers cannot serve in a dual capacity for the same transaction.

```html
<!DOCTYPE html>
<html lang="en">
<head>
<meta charset="utf-8">
<title>Brightpath Lending Partners – Recruitment Flyer</title>
<link href="https://fonts.googleapis.com/css2?family=Lato:ital,wght@0,400;0,700;0,900;1,700;1,900&family=Barlow:wght@600;700&display=swap" rel="stylesheet">
<style>
  :root {
    --blue: #1560a8;
    --blue-bright: #0a72bf;
    --blue-band: #3462ad;
    --blue-deep: #1b5cb0;
    --olive: #ad9f35;
    --gold: #d4aa2e;
    --frame: #f1f1f4;
    --photo-warm: #b08a6a;
    --photo-light: #e3d6cb;
    --white: #ffffff;
  }
  * { margin: 0; padding: 0; box-sizing: border-box; }
  html, body { width: 900px; height: 1200px; overflow: hidden; background: var(--white); }
  .flyer { position: relative; width: 900px; height: 1200px; overflow: hidden; font-family: "Lato", sans-serif; }
  .flyer-shapes { position: absolute; inset: 0; }
  .audience {
    position: absolute; left: 62px; top: 24px;
    color: var(--white); font-weight: 900; font-size: 20px; letter-spacing: 4px;
  }
  .headline {
    position: absolute; left: 61px; top: 60px;
    color: var(--white); font-weight: 700; font-size: 39px; line-height: 48px;
    letter-spacing: -0.5px;
  }
  .offer {
    position: absolute; right: 29px; top: 385px; text-align: right;
    font-family: "Barlow", sans-serif; font-weight: 700; color: var(--white);
  }
  .offer-line { font-size: 42px; line-height: 54px; }
  .offer-figure { font-size: 104px; line-height: 100px; font-weight: 600; letter-spacing: -2px; }
  .perks {
    position: absolute; left: 62px; top: 874px; list-style: none;
    color: var(--blue); font-weight: 700; font-size: 21px; line-height: 27.5px;
  }
  .perks li::before { content: "•"; display: inline-block; width: 21px; font-size: 16px; vertical-align: 2px; }
  .divider { position: absolute; left: 0; top: 1012px; width: 433px; height: 3px; background: var(--blue); }
  .phone { position: absolute; left: 61px; top: 1018px; color: var(--blue); font-weight: 700; font-size: 31px; }
  .license { position: absolute; right: 494px; top: 1060px; color: var(--blue); font-weight: 900; font-style: italic; font-size: 17px; }
  .brand {
    position: absolute; left: 496px; top: 900px; width: 390px;
    display: flex; align-items: center; gap: 12px;
    color: var(--blue); font-weight: 900; font-size: 20px; line-height: 26px; white-space: nowrap;
  }
  .brand-dot { flex: none; width: 34px; height: 34px; border-radius: 50%; background: var(--olive); }
  .pitch {
    position: absolute; left: 496px; top: 952px; width: 380px;
    color: var(--blue); font-weight: 700; font-style: italic; font-size: 16px; line-height: 22px;
  }
  .footer { position: absolute; top: 1104px; color: var(--white); font-size: 18px; line-height: 26px; }
  .footer strong { font-weight: 700; display: block; }
  .footer-resume { left: 61px; }
  .footer-address { left: 420px; }
  .small-print {
    position: absolute; left: 61px; top: 1170px; width: 810px;
    color: var(--white); font-size: 10.5px; line-height: 14px; opacity: 0.9;
  }
</style>
</head>
<body>
<main class="flyer">
  <svg class="flyer-shapes" width="900" height="1200" viewBox="0 0 900 1200">
    <polygon class="accent-gold" points="520,160 870,34 900,20 900,800 508,795 630,200" fill="var(--gold)"/>
    <polygon class="accent-olive" points="640,190 900,45 900,770 512,760 520,715 650,195" fill="var(--olive)"/>
    <polygon class="photo-frame" points="0,130 495,138 668,186 555,775 455,900 0,790" fill="var(--frame)"/>
    <defs>
      <linearGradient id="photoTone" x1="0" y1="0" x2="1" y2="1">
        <stop offset="0" stop-color="var(--photo-light)"/>
        <stop offset="0.55" stop-color="var(--photo-warm)"/>
        <stop offset="1" stop-color="#8a6c55"/>
      </linearGradient>
    </defs>
    <polygon class="photo" role="img" aria-label="Photo of two smiling colleagues seated at a table in a bright office" points="0,140 488,147 653,193 440,870 0,776" fill="url(#photoTone)"/>
    <polygon class="header-band" points="0,0 861,0 870,34 488,147 61,266 0,84" fill="var(--blue)"/>
    <polygon class="header-accent" points="870,34 488,147 560,150 873,30" fill="var(--blue-bright)"/>
    <polygon class="footer-wedge" points="0,1068 338,1103 0,1124" fill="var(--blue-deep)"/>
    <polygon class="footer-band" points="0,1124 338,1103 900,1068 900,1200 0,1200" fill="var(--blue-band)"/>
  </svg>

  <p class="audience">HOMEBROKERS</p>
  <h1 class="headline">If You Open The Brightpath Door,<br>We'll Carry<br>The Load</h1>

  <div class="offer">
    <div class="offer-line">WE</div>
    <div class="offer-line">REIMBURSE</div>
    <div class="offer-figure">100%</div>
    <div class="offer-line">OF LICENSING</div>
    <div class="offer-line">COSTS</div>
  </div>

  <ul class="perks">
    <li>Immediate Payouts</li>
    <li>Up to 75% Commission Split</li>
    <li>No Goals or Quotas</li>
    <li>Manage Your Own Schedule</li>
    <li>Work from Home</li>
  </ul>

  <div class="divider"></div>
  <p class="phone">(800) 461-9027 Ext. 23</p>
  <p class="license">NMLS #318764</p>

  <div class="brand">
    <span class="brand-dot"></span>
    <span class="brand-name">Brightpath Lending Partners, Inc.</span>
  </div>
  <p class="pitch">If you can send a text message, you can earn Mortgage Originator Income too...</p>

  <div class="footer footer-resume">
    <strong>SEND RESUME:</strong>
    Careers@brightpathlendmail.com
  </div>
  <div class="footer footer-address">
    <strong>Brightpath Lending Partners, Inc.</strong>
    7200 Marlowe Avenue, Ellicott City, MD 21046
  </div>
  <p class="small-print">**Dual income requirements governed by state law. In most cases, Homebrokers cannot serve in a dual capacity for the same transaction.</p>
</main>
</body>
</html>
```